"Harbor Builders" is a residential building company and needs a new business card design and may re

We would like a redesign based on the existing logo, and would like to see a new font as well. We are bespoke home builders who build sustainable energy efficient homes.

Industry/Entity Type

Construction

Contact Information for Business Card

Business card size 40mm x 90mm

Colors

Designer to choose colors to be used in the design.

```html
<!DOCTYPE html>
<html lang="en">
<head>
<meta charset="utf-8">
<title>Harbor Builders – Business Card</title>
<link rel="stylesheet" href="https://fonts.googleapis.com/css2?family=Montserrat:wght@600;700&family=Work+Sans:wght@400;500&display=swap">
<style>
  :root {
    --page: #2a2a2c;
    --card: #1c1c1d;
    --blue: #2b4596;
    --orange: #f08a24;
    --text: #e6e6e6;
    --muted: #cfcfcf;
  }
  * { box-sizing: border-box; margin: 0; padding: 0; }
  html, body { width: 1200px; height: 900px; overflow: hidden; }
  body {
    background: var(--page);
    display: flex; flex-direction: column; align-items: center; justify-content: center;
    gap: 40px;
    font-family: "Work Sans", Arial, sans-serif;
  }
  .card {
    width: 660px; height: 380px;
    background: var(--card);
    box-shadow: 0 12px 30px rgba(0,0,0,.45);
    position: relative;
  }
  .card-front { display: flex; align-items: center; justify-content: center; }
  .brand { display: flex; align-items: center; gap: 16px; }
  .brand-square { width: 34px; height: 34px; background: var(--orange); }
  .brand-name {
    font-family: "Montserrat", Arial, sans-serif; font-weight: 700;
    color: var(--blue); letter-spacing: 2px; font-size: 28px; text-transform: uppercase;
  }
  .card-back { display: flex; align-items: center; padding: 0 40px 0 50px; }
  .back-brand { width: 250px; flex-direction: column; align-items: flex-start; gap: 14px; }
  .back-brand .brand-square { width: 70px; height: 70px; }
  .back-brand .brand-name { font-size: 24px; line-height: 1.2; }
  .divider { width: 2px; height: 230px; background: var(--orange); margin: 0 26px 0 10px; }
  .details { color: var(--muted); font-size: 15px; line-height: 1.35; }
  .person-name {
    font-family: "Montserrat", Arial, sans-serif; font-weight: 600;
    color: var(--blue); font-size: 22px; text-transform: uppercase; letter-spacing: .5px;
  }
  .person-role { color: #fff; font-size: 16px; margin-bottom: 14px; }
  .label { color: var(--orange); }
  .reg { margin-bottom: 14px; }
  .address { margin-bottom: 14px; }
  .contact { list-style: none; }
  .contact li { display: flex; align-items: center; gap: 12px; }
  .contact svg { width: 15px; height: 15px; flex: none; }
  .accent { color: var(--orange); }
</style>
</head>
<body>
  <section class="card card-front">
    <div class="brand">
      <span class="brand-square"></span>
      <span class="brand-name">Harbor Builders</span>
    </div>
  </section>

  <section class="card card-back">
    <div class="brand back-brand">
      <span class="brand-square"></span>
      <span class="brand-name">Harbor Builders</span>
    </div>
    <span class="divider"></span>
    <div class="details">
      <p class="person-name">Daniel Moretti</p>
      <p class="person-role">Founder</p>
      <p class="reg"><span class="label">Registration</span>-40518<br><span class="label">ABN:</span> 52 804 317 669</p>
      <p class="address">PO Box 2210 Eastgate<br>LPO Bayview WA 6100</p>
      <ul class="contact">
        <li>
          <svg viewBox="0 0 16 16" aria-hidden="true"><path d="M4 1l3 3-2 2c1 2 3 4 5 5l2-2 3 3-2 2C7 14 2 9 2 3z" fill="var(--orange)"/></svg>
          <span>0400 555 018</span>
        </li>
        <li>
          <svg viewBox="0 0 16 16" aria-hidden="true"><rect x="1" y="3" width="14" height="10" fill="var(--orange)"/><path d="M1 3l7 6 7-6" stroke="#1c1c1d" stroke-width="1.4" fill="none"/></svg>
          <span>daniel@harborbuilders.com.au</span>
        </li>
        <li>
          <svg viewBox="0 0 16 16" aria-hidden="true"><g fill="none" stroke="var(--orange)" stroke-width="1.3"><circle cx="8" cy="8" r="6.5"/><ellipse cx="8" cy="8" rx="3" ry="6.5"/><path d="M1.5 8h13"/></g></svg>
          <span>www.<span class="accent">harborbuilders.com</span>.au</span>
        </li>
      </ul>
    </div>
  </section>
</body>
</html>
```